professional business card design

Business card design. Photos have been uploaded and i am open to the designer choosing which photos to use. Would like the card to be mostyly in a grey scale design with black, whites, silver & grey colours. I have added copy of our flyer as would like on the back side of card our services to be listed. Do not use any bright colurs such as blue red green or yellow. i need to be able to edit the phone number and naem in the final card design submitted.

Target Market(s)

Clients

Industry/Entity Type

earhmovibng and transport

Contact Information for Business Card

Director Name, address, email, phone number and services

Colors

Designer to choose only greyscale colors for use in the design.

Requirements
Should not have
• no yellow, red, blue or green

```html
<!DOCTYPE html>
<html lang="en">
<head>
<meta charset="utf-8">
<title>RHS Business Card</title>
<link href="https://fonts.googleapis.com/css2?family=Poppins:wght@400;600;700&family=Arimo:wght@400;700&display=swap" rel="stylesheet">
<style>
  :root {
    --stage: #1d1d1e;
    --card: #111112;
    --card-edge: #1a1a1b;
    --white: #ffffff;
    --light: #d9d9d9;
    --grey: #9a9a9a;
    --silver: #c4c4c6;
    --rule: #4a4a4a;
  }
  * { box-sizing: border-box; margin: 0; padding: 0; }
  html, body { width: 1200px; height: 900px; overflow: hidden; }
  body {
    background: radial-gradient(ellipse at 50% 40%, #2a2a2b 0%, var(--stage) 70%);
    font-family: "Arimo", Arial, sans-serif;
    position: relative;
  }
  .card {
    position: absolute;
    width: 540px;
    height: 310px;
    background: linear-gradient(145deg, var(--card-edge) 0%, var(--card) 55%, #0b0b0c 100%);
    box-shadow: 0 18px 40px rgba(0,0,0,.65);
    overflow: hidden;
  }
  /* Front */
  .card-front { left: 40px; top: 470px; }
  .brand-mark {
    position: absolute;
    left: 40px; top: 118px;
    width: 180px;
    display: flex; align-items: center; gap: 12px;
    font-family: "Poppins", sans-serif;
    font-weight: 700;
    font-size: 54px;
    letter-spacing: 2px;
    color: var(--silver);
  }
  .brand-mark .dot {
    width: 14px; height: 14px; border-radius: 50%;
    background: var(--silver);
  }
  .divider {
    position: absolute;
    left: 238px; top: 70px;
    width: 1px; height: 170px;
    background: var(--rule);
  }
  .contact {
    position: absolute;
    left: 262px; top: 62px;
    color: var(--white);
  }
  .contact .name {
    font-family: "Poppins", sans-serif;
    font-weight: 700; font-size: 19px; letter-spacing: .5px;
  }
  .contact .role {
    font-family: "Poppins", sans-serif;
    font-size: 13px; color: var(--grey); margin-bottom: 12px;
  }
  .contact .line {
    display: flex; align-items: center; gap: 8px;
    font-size: 13px; color: var(--light); margin-bottom: 4px;
  }
  .contact .line svg { width: 13px; height: 13px; flex: none; }
  .contact .company {
    font-family: "Poppins", sans-serif;
    font-weight: 700; font-size: 14px; margin-top: 10px;
  }
  .contact .address { font-size: 13px; color: var(--grey); line-height: 1.35; }

  /* Back */
  .card-back { left: 620px; top: 120px; }
  .services {
    position: absolute;
    left: 28px; top: 34px;
    color: var(--white);
  }
  .services h2 {
    font-family: "Poppins", sans-serif;
    font-weight: 700; font-size: 14px; margin-bottom: 4px;
  }
  .services ul { list-style: none; }
  .services li {
    font-size: 11.5px; line-height: 14.5px; color: var(--light);
    padding-left: 12px; position: relative;
  }
  .services li::before {
    content: ""; position: absolute; left: 1px; top: 4px;
    width: 6px; height: 6px; border-radius: 50%; background: var(--white);
  }
  .services .note {
    margin-top: 8px; font-size: 11.5px; line-height: 14px; color: var(--white);
    width: 300px;
  }
  .card-back .brand-mark {
    left: auto; right: 30px; top: 26px; width: auto;
    font-size: 44px;
  }
  .truck-photo {
    position: absolute;
    right: 0; top: 105px;
    width: 230px; height: 140px;
    background: radial-gradient(ellipse at 65% 50%, #5b5e63 0%, #34363a 45%, rgba(17,17,18,0) 75%);
  }
</style>
</head>
<body>

  <section class="card card-front">
    <div class="brand-mark"><span class="dot"></span>RHS</div>
    <div class="divider"></div>
    <div class="contact">
      <p class="name">DANIEL HARKER</p>
      <p class="role">Director</p>
      <p class="line">
        <svg viewBox="0 0 24 24" aria-hidden="true"><path fill="#fff" d="M6.6 10.8a15.1 15.1 0 0 0 6.6 6.6l2.2-2.2a1 1 0 0 1 1-.25 11.4 11.4 0 0 0 3.6.57 1 1 0 0 1 1 1V20a1 1 0 0 1-1 1A17 17 0 0 1 3 4a1 1 0 0 1 1-1h3.5a1 1 0 0 1 1 1c0 1.25.2 2.45.57 3.57a1 1 0 0 1-.25 1z"/></svg>
        000 555 000
      </p>
      <p class="line">
        <svg viewBox="0 0 24 24" aria-hidden="true"><path fill="#fff" d="M2 5h20v14H2z"/><path fill="none" stroke="#111" stroke-width="1.6" d="M2.5 5.5 12 13l9.5-7.5"/></svg>
        email@ridgelinehaulage.com.au
      </p>
      <p class="line">
        <svg viewBox="0 0 24 24" aria-hidden="true"><circle cx="12" cy="12" r="10" fill="none" stroke="#fff" stroke-width="2"/><ellipse cx="12" cy="12" rx="4.5" ry="10" fill="none" stroke="#fff" stroke-width="1.6"/><path stroke="#fff" stroke-width="1.6" d="M2 12h20M4 7h16M4 17h16"/></svg>
        www.websiteaddress.com
      </p>
      <p class="company">RHS PTY LTD</p>
      <p class="address">rhs lot 114, ironbark track<br>yarrowvale, Australia</p>
    </div>
  </section>

  <section class="card card-back">
    <div class="brand-mark"><span class="dot"></span>RHS</div>
    <div class="truck-photo" role="img" aria-label="Photo of a road train tanker truck"></div>
    <div class="services">
      <h2>OUR SERVICES</h2>
      <ul>
        <li>Over size loads/hot shot loads</li>
        <li>Heavy vehicle recovery services</li>
        <li>Potable water deliveries</li>
        <li>Road building/mainttenance</li>
        <li>Earthworks</li>
        <li>Sand &amp; metal supply &amp; cartage</li>
        <li>Road train tippers</li>
        <li>Road train tankers</li>
        <li>Road train flat tops</li>
        <li>Drop deck trailers</li>
        <li>Mine site accredited</li>
        <li>Equipment &amp; operators</li>
      </ul>
      <p class="note">we offer a large range of services not listed so call us today for a personalised quote to suit your needs.</p>
    </div>
  </section>

</body>
</html>
```